Upscale business cards needed for Board of Directors

We need professional business cards created for members of our family business Board of Directors. We would like these relatively simple and straightforward, but also with a unique element to set them apart. Probably stick with neutral and simple colors - white, grey etc. We need space for the traditional elements, including name, title, address, email/phone number. And we will be creating several from this template so it needs to be template that is easy to switch information in and out of.
Business
See description

```html
<!DOCTYPE html>
<html lang="en">
<head>
<meta charset="utf-8">
<title>Harborline Holdings – Business Card</title>
<link href="https://fonts.googleapis.com/css2?family=Arimo:wght@400&display=swap" rel="stylesheet">
<style>
  :root {
    --page: #e7e5e1;
    --card-white: #fbfbfa;
    --ink: #2a2627;
    --charcoal: #2b2728;
    --gold: #c8bd9c;
    --light-text: #efece6;
    --card-shadow: 0 6px 18px rgba(0,0,0,0.18);
  }
  * { margin: 0; padding: 0; box-sizing: border-box; }
  html, body { width: 1200px; height: 858px; overflow: hidden; background: var(--page); }
  .stage { position: relative; width: 1200px; height: 858px; }
  .card {
    position: absolute; top: 275px; width: 540px; height: 309px;
    background: var(--card-white); box-shadow: var(--card-shadow); overflow: hidden;
  }
  .card--front { left: 40px; }
  .card--back { left: 620px; }
  .card__wave { position: absolute; inset: 0; width: 540px; height: 309px; }
  .company-name {
    position: absolute; font-family: "Arimo", sans-serif; font-weight: 400;
    color: var(--ink); font-size: 32px; line-height: 1; white-space: nowrap;
  }
  .card--front .company-name { left: 34px; top: 52px; }
  .card--back .company-name { left: 50%; top: 50%; transform: translate(-50%, -50%); }
  .person { position: absolute; left: 30px; bottom: 22px; font-family: "Arimo", sans-serif; }
  .person__name { color: var(--light-text); font-size: 20px; }
  .person__title { color: var(--gold); font-size: 15px; margin-top: 4px; }
  .divider { position: absolute; left: 198px; bottom: 18px; width: 2px; height: 74px; background: var(--light-text); }
  .contacts { position: absolute; left: 218px; bottom: 20px; list-style: none; font-family: "Arimo", sans-serif; color: var(--light-text); font-size: 15px; }
  .contacts li { display: flex; align-items: center; gap: 9px; height: 24px; }
  .contacts svg { width: 15px; height: 15px; flex: none; }
</style>
</head>
<body>
<main class="stage">
  <section class="card card--front" aria-label="Business card front">
    <svg class="card__wave" viewBox="0 0 540 309" aria-hidden="true">
      <path d="M0,228 C150,238 240,205 295,158 S440,66 540,58" fill="none" stroke="var(--gold)" stroke-width="7"/>
      <path d="M0,242 C150,252 250,218 305,170 S450,80 540,72 L540,309 L0,309 Z" fill="var(--charcoal)"/>
    </svg>
    <p class="company-name">Harborline Holdings</p>
    <div class="person">
      <p class="person__name">Owen Hartley</p>
      <p class="person__title">Managing Director</p>
    </div>
    <span class="divider"></span>
    <ul class="contacts">
      <li>
        <svg viewBox="0 0 15 15" aria-hidden="true"><rect width="15" height="15" fill="var(--gold)"/><path d="M4.5,3.5 l2,0 0.6,2.2 -1.2,0.9 q0.9,1.8 2.5,2.6 l0.9,-1.2 2.2,0.6 0,2 q-5.5,0.5 -7,-7.1z" fill="var(--charcoal)"/></svg>
        <span>021-555-0147</span>
      </li>
      <li>
        <svg viewBox="0 0 15 15" aria-hidden="true"><rect width="15" height="15" fill="var(--gold)"/><rect x="3" y="4.5" width="9" height="6.5" fill="none" stroke="var(--charcoal)" stroke-width="1.2"/><path d="M3,4.5 L7.5,8.3 L12,4.5" fill="none" stroke="var(--charcoal)" stroke-width="1.2"/></svg>
        <span>hello@harborline.com</span>
      </li>
      <li>
        <svg viewBox="0 0 15 15" aria-hidden="true"><rect width="15" height="15" fill="var(--gold)"/><path d="M7.5,12.5 C5,9.5 4.3,8 4.3,6.3 a3.2,3.2 0 0 1 6.4,0 c0,1.7 -0.7,3.2 -3.2,6.2z" fill="var(--charcoal)"/><circle cx="7.5" cy="6.3" r="1.2" fill="var(--gold)"/></svg>
        <span>480 N Calder Rd</span>
      </li>
    </ul>
  </section>

  <section class="card card--back" aria-label="Business card back">
    <p class="company-name">Harborline Holdings</p>
  </section>
</main>
</body>
</html>
```